VFX Company Business Card Design Project

The Kestrel Works is a decentralized Visual Effects Studio servicing the television and feature film industries.
Project Brief:
Take our logo that was previously designed on Pencil Harbor and make a double sided business card.
Requirements:
- Card MUST be double sided.
- Front of card MUST have the yellow part of our logo against the dark grey background.
- Back of card is completely up to the designer.
- Back of card must include the complete company logo.
Please follow these File Preparation guidelines:
http://printnook.ca/infopage?file=filetype_en&s=PrintNook_new&lang=en
Business

```html
<!DOCTYPE html>
<html lang="en">
<head>
<meta charset="utf-8">
<title>The Kestrel Works — Business Cards</title>
<link rel="stylesheet" href="https://fonts.googleapis.com/css2?family=Questrial&family=Jost:wght@400;500;600&display=swap">
<style>
  :root {
    --backdrop: #8b3f1c;
    --card-dark: #262626;
    --card-light: #e9eee4;
    --card-slate: #5f6b6e;
    --brand-yellow: #f8c22a;
    --ink-dark: #1f1f1f;
    --ink-light: #ffffff;
    --ink-soft: #e6e6e6;
    --band: #e9eee4;
    --card-edge: rgba(0,0,0,0.55);
  }
  * { box-sizing: border-box; margin: 0; padding: 0; }
  html, body {
    width: 1200px; height: 733px; overflow: hidden;
    background: var(--backdrop);
  }
  .sheet { position: relative; width: 1200px; height: 733px; }
  .card {
    position: absolute;
    border-radius: 22px;
    border: 1px solid var(--card-edge);
    overflow: hidden;
    font-family: "Questrial", sans-serif;
  }
  .card--front { left: 70px; top: 44px; width: 523px; height: 298px; background: var(--card-dark); }
  .card--contact { left: 630px; top: 48px; width: 525px; height: 299px; background: var(--card-dark); }
  .card--back-light { left: 66px; top: 385px; width: 524px; height: 298px; background: var(--card-light); }
  .card--back-slate { left: 625px; top: 389px; width: 522px; height: 298px; background: var(--card-slate); }

  .brand-name {
    position: absolute; left: 0; right: 0; text-align: center;
    font-family: "Questrial", sans-serif; white-space: nowrap;
  }
  .card--front .brand-name { top: 118px; font-size: 50px; color: var(--brand-yellow); }
  .card--back-light .brand-name { top: 110px; font-size: 44px; color: var(--ink-dark); }
  .card--back-slate .brand-name { top: 104px; font-size: 48px; color: var(--ink-light); }

  .web-line {
    position: absolute; left: 0; right: 0; text-align: center;
    font-family: "Jost", sans-serif; font-size: 18px; letter-spacing: 2.5px;
  }
  .card--back-light .web-line { top: 253px; color: var(--ink-dark); }
  .card--back-slate .web-line { top: 255px; color: var(--ink-light); }

  .contact-brand {
    position: absolute; left: 30px; top: 94px; width: 260px;
    text-align: center; font-size: 27px; color: var(--ink-soft); white-space: nowrap;
  }
  .contact-divider {
    position: absolute; left: 296px; top: 58px; width: 2px; height: 130px;
    background: var(--ink-soft); opacity: 0.8;
  }
  .contact-details { position: absolute; left: 313px; top: 48px; color: var(--ink-light); font-family: "Jost", sans-serif; }
  .contact-name { font-size: 20px; font-weight: 600; }
  .contact-title { font-size: 15px; margin-top: 1px; margin-bottom: 10px; }
  .contact-row { display: flex; align-items: center; gap: 6px; font-size: 14px; line-height: 21px; }
  .contact-row svg { width: 11px; height: 11px; flex: none; }
  .address-rule { position: absolute; left: 0; right: 0; height: 2px; background: var(--band); }
  .address-rule--top { top: 228px; }
  .address-rule--bottom { top: 266px; }
  .address-band {
    position: absolute; left: 0; right: 0; top: 234px; height: 29px;
    background: var(--band); color: var(--ink-dark);
    font-family: "Jost", sans-serif; font-size: 14px; letter-spacing: 1px;
    text-align: center; line-height: 29px;
  }
</style>
</head>
<body>
<main class="sheet">
  <section class="card card--front" aria-label="Card front">
    <p class="brand-name">The Kestrel Works</p>
  </section>

  <section class="card card--contact" aria-label="Card back with contact details">
    <p class="contact-brand">The Kestrel Works</p>
    <div class="contact-divider"></div>
    <div class="contact-details">
      <p class="contact-name">Your Name</p>
      <p class="contact-title">Title</p>
      <p class="contact-row">
        <svg viewBox="0 0 12 12"><path d="M2 1l2 0 1 3-1.3 1a6 6 0 0 0 3.3 3.3L8 7l3 1v2c0 .6-.4 1-1 1A9 9 0 0 1 1 2c0-.6.4-1 1-1z" fill="none" stroke="#fff" stroke-width="1"/></svg>
        0987 654321</p>
      <p class="contact-row">
        <svg viewBox="0 0 12 12"><rect x="1" y="4" width="10" height="6" rx="1.5" fill="#fff"/><path d="M3 4l1-2h4l1 2" fill="none" stroke="#fff"/></svg>
        0987 654321</p>
      <p class="contact-row">
        <svg viewBox="0 0 12 12"><rect x="1" y="3" width="10" height="7" fill="#fff"/><path d="M1 3l5 4 5-4" fill="none" stroke="#262626"/></svg>
        info@kestrelworks.com</p>
      <p class="contact-row">
        <svg viewBox="0 0 12 12"><circle cx="6" cy="6" r="5" fill="none" stroke="#fff"/><path d="M1 6h10M6 1c-2.5 3-2.5 7 0 10M6 1c2.5 3 2.5 7 0 10" fill="none" stroke="#fff" stroke-width=".8"/></svg>
        www.kestrelworks.com</p>
    </div>
    <div class="address-rule address-rule--top"></div>
    <p class="address-band">00, Complex name, City, State 0042</p>
    <div class="address-rule address-rule--bottom"></div>
  </section>

  <section class="card card--back-light" aria-label="Card back, light">
    <p class="brand-name">The Kestrel Works</p>
    <p class="web-line">www.kestrelworks.com</p>
  </section>

  <section class="card card--back-slate" aria-label="Card back, slate">
    <p class="brand-name">The Kestrel Works</p>
    <p class="web-line">www.kestrelworks.com</p>
  </section>
</main>
</body>
</html>
```